Standardize Word Documents

Hello - I'd like for these documents to look consistent in Microsoft Word. The deliverable needs to be in Word so we can edit if needed.

```html
<!DOCTYPE html>
<html lang="en">
<head>
<meta charset="utf-8">
<title>Harbor Crest Properties – Policy Document Set</title>
<link rel="stylesheet" href="https://fonts.googleapis.com/css2?family=Carlito:ital,wght@0,400;0,700;1,400&family=Open+Sans:wght@400&display=swap">
<style>
  :root{
    --bg:#e9e9e9;
    --paper:#ffffff;
    --paper-tint:#f1f2f4;
    --navy:#1d3b6e;
    --blue:#2a5a9a;
    --rule:#5b85bd;
    --ink:#3a3a3a;
    --label:#9b9b9b;
    --accent:#4a8fd0;
  }
  html,body{margin:0;padding:0;overflow:hidden;}
  body{background:var(--bg);}
  .canvas{position:relative;width:1176px;height:1200px;overflow:hidden;background:var(--bg);}
  .file-label{position:absolute;left:34px;font:400 13px/1 "Open Sans",sans-serif;color:var(--label);letter-spacing:.4px;}

  .page{position:absolute;width:188px;height:267px;
    background:radial-gradient(ellipse at 80% 15%,var(--paper-tint) 0%,var(--paper) 45%),var(--paper);
    box-shadow:0 7px 6px -4px rgba(0,0,0,.35);overflow:hidden;}
  .brand-corner{position:absolute;left:5px;top:6px;display:flex;align-items:center;gap:2px;}
  .brand-corner .sq{width:8px;height:8px;background:var(--navy);}
  .brand-corner span{font:700 4px/1 Carlito,sans-serif;color:var(--navy);}
  .head-rule{position:absolute;top:19px;left:28px;right:0;height:.6px;background:var(--rule);}
  .foot-rule{position:absolute;bottom:17px;left:0;right:0;height:.6px;background:var(--navy);}
  .page-no{position:absolute;bottom:11px;left:22px;font:400 2.6px/1 Carlito,sans-serif;color:#555;}
  .foot-brand{position:absolute;bottom:14px;right:22px;display:flex;align-items:center;gap:1.5px;background:var(--paper);padding:0 2px;}
  .foot-brand .dot{width:6px;height:6px;border-radius:50%;background:var(--navy);}
  .foot-brand span{font:700 4px/1 Carlito,sans-serif;color:var(--navy);}

  .content{position:absolute;top:30px;left:22px;right:22px;bottom:26px;overflow:hidden;
    font:400 2.8px/1.38 Carlito,sans-serif;color:var(--ink);text-align:justify;}
  .content p{margin:0 0 2.3px;}
  .content ul{margin:0 0 2.3px;padding-left:9px;}
  .content li{margin-bottom:.8px;}
  .content .spaced li{margin-bottom:3.2px;}
  .doc-title{font:700 6.2px/1.1 Carlito,sans-serif;color:var(--blue);text-align:center;margin:3px 0 .6px;}
  .doc-sub{font:700 2.6px/1.2 Carlito,sans-serif;color:var(--navy);text-align:center;text-transform:uppercase;margin-bottom:3.5px;}
  .doc-sub.blue{color:var(--blue);font-size:3.4px;}
  .sec{font:700 2.9px/1.3 Carlito,sans-serif;color:var(--blue);text-transform:uppercase;margin:3px 0 1.6px;}
  .sub-sec{font:700 2.7px/1.3 Carlito,sans-serif;color:var(--blue);text-transform:uppercase;margin:2px 0 1.2px 11px;}
  .indent{padding-left:11px;}
  .lead{font:700 3.6px/1.3 Carlito,sans-serif;color:var(--blue);margin:3px 0 2px;}
  .lead.sm{font-size:2.9px;}
  .adopted{font-style:italic;margin-top:12px;}
  .link{color:var(--blue);text-decoration:underline;}

  /* workforce infographic */
  .stats{display:grid;grid-template-columns:1fr 1fr;column-gap:6px;margin-bottom:4px;text-align:left;}
  .stat-title{font:700 4.6px/1 Carlito,sans-serif;color:var(--blue);text-transform:uppercase;margin:1px 0 2px;}
  .total{display:flex;align-items:center;gap:3px;}
  .total .t{font:700 4.4px/1 Carlito,sans-serif;color:var(--blue);}
  .total .n{font:700 13px/1 Carlito,sans-serif;color:#111;}
  .gender{display:flex;gap:6px;}
  .gender div{text-align:center;font:400 2.4px/1.2 Carlito,sans-serif;}
  .gender .ring{width:10px;height:10px;border-radius:50%;border:1.6px solid var(--blue);display:flex;align-items:center;justify-content:center;font:700 2.6px/1 Carlito,sans-serif;margin:1px auto 0;}
  .people{width:40px;height:14px;background:linear-gradient(90deg,#6f9ed3,#1d3b6e);border-radius:1px;}
  .small-note{font:700 2.4px/1.25 Carlito,sans-serif;color:#222;}
</style>
</head>
<body>
<div class="canvas">

  <div class="file-label" style="top:130px">FILE 1</div>
  <div class="file-label" style="top:436px">FILE 2</div>
  <div class="file-label" style="top:728px">FILE 3</div>
  <div class="file-label" style="top:1020px">FILE 4</div>

  <!-- FILE 1 · Environmental Sustainability Policy -->
  <section class="page" style="left:105px;top:25px">
    <div class="brand-corner"><div class="sq"></div><span>HCP</span></div><div class="head-rule"></div>
    <div class="content">
      <div class="doc-title">HARBOR CREST PROPERTIES, INC.</div>
      <div class="doc-sub">Environmental Sustainability Policy</div>
      <p>As owner and capital provider to over 200 properties, Harbor Crest recognizes the impact the real estate sector can have on our planet and its natural resources through land change, energy use, greenhouse gas emissions, and other environmental factors.</p>
      <p>Harbor Crest is committed to implementing environmentally sustainable best practices for our own operations, and to encouraging, incentivizing and assisting our lessees and borrowers ("operators") in their efforts to address environmental opportunities and challenges. Through sustainable practices and operator support, we are taking action to reduce our impact and the impact of our properties and those who use them.</p>
      <p>The development and maintenance of our environmental policies and programs is a company-wide effort led by an internal working group and our executive team. We will review and evaluate this policy at least annually. All employees will receive a copy of this policy.</p>
      <p>In addition, the Environmental, Social and Governance Committee (the "Committee") of the Board of Directors oversees the progress of our environmental policies and programs. The Charter of the Committee explains its purpose and responsibilities and is accessible on our website at www.harborcrest.example.</p>
      <div class="lead">We strive to conduct our overall business in an environmentally sustainable manner by:</div>
      <ul>
        <li>Operating in a commercially responsible manner that respects the environment.</li>
        <li>Complying with all applicable environmental laws and regulations.</li>
        <li>Surveying our operators to better understand their environmental awareness and needs, and identifying opportunities to support and incentivize their initiatives, including sustainable building improvements.</li>
        <li>Aligning with the Sustainability Accounting Standards Board real estate framework to guide us as we provide our shareholders with relevant information on our environmental impact.</li>
        <li>Communicating this policy to shareholders, employees, operators, vendors, and the public via our website.</li>
      </ul>
      <p>The majority of our operators conduct business under a triple-net structure and are generally responsible for maintaining the properties in our portfolio, including environmentally sustainable practices. Under this structure we cannot control operations, however we can encourage and support our operators by promoting sustainable best practices, recommending environmentally friendly products and vendors, and financing environmental initiatives at attractive rates.</p>
    </div>
    <div class="foot-rule"></div><div class="page-no">Page | 1</div>
    <div class="foot-brand"><div class="dot"></div><span>HCP</span></div>
  </section>

  <section class="page" style="left:318px;top:25px">
    <div class="brand-corner"><div class="sq"></div><span>HCP</span></div><div class="head-rule"></div>
    <div class="content">
      <div class="lead sm" style="margin-top:5px">How We Support Our Operators' Environmental Efforts</div>
      <ul class="spaced">
        <li>We provide financial incentives for environmentally sound, mutually beneficial upgrade initiatives.</li>
        <li>We evaluate and consider climate risk considerations in new investments and portfolio management, including earthquake, fire, heat, storm, and flood.</li>
        <li>We obtain Phase I (and Phase II, if applicable) environmental reports, geotechnical and soils reports, zoning reports and wetlands delineation as part of our diligence procedures when acquiring properties, and we attempt to avoid buying real estate with known high-risk catastrophic environmental events and or environmental contamination.</li>
        <li>We collect data from participating operating partners annually to monitor and report energy and water consumption and recycling initiatives, among other self-reported environmentally sustainable initiatives.</li>
        <li>We incorporate Green Lease language into new and amended leases.</li>
      </ul>
      <p>Throughout our organization, we embrace this commitment to environmental and sustainable practices, including in our corporate-level initiatives.</p>
    </div>
    <div class="foot-rule"></div><div class="page-no">Page | 2</div>
    <div class="foot-brand"><div class="dot"></div><span>HCP</span></div>
  </section>

  <section class="page" style="left:531px;top:25px">
    <div class="brand-corner"><div class="sq"></div><span>HCP</span></div><div class="head-rule"></div>
    <div class="content">
      <div class="lead sm" style="margin-top:1px">Highlights of corporate-level initiatives:</div>
      <ul class="spaced">
        <li>Our corporate headquarters' energy efficiency features include automatic lights, internal temperature controls, automatic HVAC controls on evenings and weekends, power saver mode on printer and copy machines, automatic faucets, and toilets.</li>
        <li>Our corporate headquarters provides employees with tri-temp purified water from reverse osmosis water systems. These systems are plumbed into the wall, eliminating the need for plastic or glass refill bottles while also reducing the use of single-serve plastic bottled waters. We provide our team water bottles from recycled glass.</li>
        <li>Our document retention practice strives to reduce paper usage and encourages electronic file sharing.</li>
        <li>We participate in a recycling program that encourages our employees to reduce, reuse and recycle waste.</li>
        <li>We participate in a regional clean power program, an opt-in program that acquires and delivers green energy supply (solar, wind, water) sourced locally and regionally.</li>
        <li>We purchase carbon offsets for employee travel and our corporate office space on a quarterly basis.</li>
        <li>Hand sanitizer is available throughout our office space.</li>
        <li>Rather than sending checks, we send wire transfers reducing the impact of check writing and mailing (carbon emissions) by more than 90%.</li>
      </ul>
      <p>All employees will receive a copy of this policy and are responsible for adhering to this policy as well as supporting our operators in their environmental efforts.</p>
      <p>Please direct questions and input about this policy to Jordan Reyes <span class="link">jordan.reyes@harborcrest.example</span>.</p>
      <p class="adopted">Adopted &nbsp;&nbsp;&nbsp;&nbsp;&nbsp;&nbsp;&nbsp;&nbsp;&nbsp;&nbsp;&nbsp;&nbsp;, 2022</p>
    </div>
    <div class="foot-rule"></div><div class="page-no">Page | 3</div>
    <div class="foot-brand"><div class="dot"></div><span>HCP</span></div>
  </section>

  <!-- FILE 2 · Human and Labor Rights Policy -->
  <section class="page" style="left:105px;top:309px">
    <div class="brand-corner"><div class="sq"></div><span>HCP</span></div><div class="head-rule"></div>
    <div class="content">
      <div class="doc-title" style="margin-top:5px">HARBOR CREST PROPERTIES, INC.</div>
      <div class="doc-sub">Human and Labor Rights Policy</div>
      <p>At Harbor Crest, we are committed to being a workplace that encourages respect, collaboration, communication, transparency, and integrity.</p>
      <p>While crafting this policy, we referenced multiple third-party international and national organizations. Whenever possible, we have aligned our approach in this policy with the following:</p>
      <ul>
        <li>International Labour Organization Conventions</li>
        <li>United Nations Sustainability Development Goals (UN SDGs)</li>
        <li>United Nations Guiding Principles on Business and Human Rights</li>
        <li>Sustainability Accounting Standards Board (SASB) Human Capital Bulletin</li>
        <li>Gender Equality Index</li>
      </ul>
      <p>The development and maintenance of this policy is a company-wide effort overseen by the Board of Directors through its Environmental, Social and Governance Committee. We will review and evaluate this policy at least annually. All employees will receive a copy of this policy. Beyond this policy, employees and directors are expected to comply with our Code of Business Conduct and Ethics, and partners, suppliers, and vendors are expected to comply with our Vendor Code of Conduct. This policy and both codes are accessible on our website at <span class="link">www.harborcrest.example</span>.</p>
      <div class="sec">Anti-Corruption</div>
      <p>Harbor Crest expects our employees and persons with whom we do business, including lessees, borrowers, and financing sources, to act ethically and with integrity. We do not tolerate corruption in any form. We will not engage in any form of corrupt practices including, without limitation, extortion, fraud, impersonation, false declarations, bribery, money laundering, supporting or involvement with terrorist or organized crime organizations or activities. Our personnel will not offer, solicit or accept bribes or kickbacks involving any government official or third party with the intention of obtaining or retaining a business advantage. We do not permit improper or excessive payments in dealing with the government or private sector. Our employees are expected to observe all government rules, regulations and restrictions on gifts and entertainment.</p>
      <div class="sec">Anti-Harassment and Non-Discrimination</div>
      <p>Harbor Crest is committed to maintaining a work environment that is free from unlawful discrimination, harassment, and retaliation. In keeping with this commitment, our company does not tolerate unlawful discrimination against, or harassment of, an applicant, employee, client, customer, or vendor based on any protected characteristic. We prohibit retaliation of any kind against an individual who complains of suspected harassment or discrimination, or who otherwise engages in protected activity.</p>
    </div>
    <div class="foot-rule"></div><div class="page-no">Page | 1</div>
    <div class="foot-brand"><div class="dot"></div><span>HCP</span></div>
  </section>

  <section class="page" style="left:318px;top:309px">
    <div class="brand-corner"><div class="sq"></div><span>HCP</span></div><div class="head-rule"></div>
    <div class="content">
      <div class="sec" style="margin-top:1px">Child Labor</div>
      <p>Harbor Crest prohibits the use of child labor in our business in accordance with International Labour Organization Convention No. 138 and related literature. We take all necessary preventative measures to ensure that they do not employ anyone under the applicable legal minimum age of employment.</p>
      <div class="sec">Compensation and Benefits</div>
      <p>Harbor Crest recognizes the importance of committing to ensuring a living wage for all employees by complying with the national wage regulations, such as the minimum wage and overtime payments.</p>
      <div class="sec">Discipline</div>
      <p>Harbor Crest objects to any form of corporal punishment, mental or physical coercion, or verbal abuse in the workplace.</p>
      <div class="sec">Diversity, Equity &amp; Inclusion</div>
      <p>Harbor Crest is an equal opportunity employer and does not discriminate based on an individual's race, gender, age, color, religion, national origin, mental or physical disability, sexual orientation, ancestry, genetic information, military or veteran status, creed, pregnancy, marital status, citizenship, gender identity, gender expression or any other status protected by applicable law. This statement extends to specifically respect and protect minority groups and women's rights under the internationally endorsed UN Guiding Principles on Business and Human Rights.</p>
      <div class="sec">Employee Safety and Health</div>
      <p>Employee safety and health is an important element of our working environment, and we are dedicated to creating and maintaining a safe and healthy working environment. A safe and healthy environment includes access to clean sanitary facilities and drinking water as a fundamental human right.</p>
      <div class="sec">Forced Labor</div>
      <p>Harbor Crest rejects the use of slavery and other forms of forced or coerced labor or servitude, including prison and human trafficking.</p>
      <div class="sec">Freedom of Association</div>
      <p>We recognize and do not interfere with our employees' right to self-organization, to form, join, or assist labor organizations, to bargain collectively through representatives of their own choosing, and to engage in other concerted activities for the purpose of collective bargaining or other mutual aid or protection.</p>
    </div>
    <div class="foot-rule"></div><div class="page-no">Page | 2</div>
    <div class="foot-brand"><div class="dot"></div><span>HCP</span></div>
  </section>

  <section class="page" style="left:531px;top:309px">
    <div class="brand-corner"><div class="sq"></div><span>HCP</span></div><div class="head-rule"></div>
    <div class="content">
      <div class="sec" style="margin-top:1px">Complaints</div>
      <p>Harbor Crest has implemented a whistleblower hotline and dedicated email address to enable all interested parties, including employees, to submit confidential complaints, concerns, unethical business practices, violations or suspected violations for all matters pertaining to accounting, internal control, or auditing. Our company will not tolerate retaliation for whistleblower reports made in good faith.</p>
      <p>Please direct questions and input about this policy to Jordan Reyes <span class="link">jordan.reyes@harborcrest.example</span>.</p>
      <p class="adopted">Adopted &nbsp;&nbsp;&nbsp;&nbsp;&nbsp;&nbsp;&nbsp;&nbsp;&nbsp;&nbsp;&nbsp;&nbsp;, 2022</p>
    </div>
    <div class="foot-rule"></div><div class="page-no">Page | 3</div>
    <div class="foot-brand"><div class="dot"></div><span>HCP</span></div>
  </section>

  <!-- FILE 3 · Human Capital Policy -->
  <section class="page" style="left:105px;top:600px">
    <div class="brand-corner"><div class="sq"></div><span>HCP</span></div><div class="head-rule"></div>
    <div class="content">
      <div class="doc-title" style="margin-top:3px;font-size:5.2px">HARBOR CREST PROPERTIES, INC.</div>
      <div class="doc-sub">Human Capital Policy</div>
      <p>At Harbor Crest, we strive to cultivate a cohesive company culture based upon ethical standards. We recognize and value our employees and are committed to being a workplace that encourages respect, collaboration, communication, transparency, and integrity. We seek to hire talented employees with diverse backgrounds and perspectives.</p>
      <p>The development and maintenance of this policy is a company-wide effort overseen by the Board of Directors through its Environmental, Social and Governance Committee. We will review and evaluate this policy at least annually. All employees will receive a copy of this policy. This policy is accessible on our website at <span class="link">www.harborcrest.example</span>.</p>
      <p>While crafting this policy, we referenced multiple third-party international and national organizations. Whenever possible, we have aligned our approach in this policy with the following:</p>
      <ul class="spaced">
        <li>International Labour Organization Conventions</li>
        <li>United Nations Sustainability Development Goals (UN SDGs)</li>
        <li>United Nations Guiding Principles on Business and Human Rights</li>
        <li>Sustainability Accounting Standards Board (SASB) Human Capital Bulletin</li>
        <li>Gender Equality Index</li>
      </ul>
      <div class="sec">Workforce Overview</div>
      <p>We endeavor to provide a working environment where all employees can have fulfilling careers that enhance our company and community.</p>
    </div>
    <div class="foot-rule"></div><div class="page-no">Page | 1</div>
    <div class="foot-brand"><div class="dot"></div><span>HCP</span></div>
  </section>

  <section class="page" style="left:318px;top:600px">
    <div class="brand-corner"><div class="sq"></div><span>HCP</span></div><div class="head-rule"></div>
    <div class="content">
      <div class="stats">
        <div>
          <div class="total"><div class="t">TOTAL<br>EMPLOYEES</div><div class="n">25</div></div>
          <div class="stat-title" style="margin-top:4px">Diversity</div>
          <svg width="70" height="38" viewBox="0 0 70 38" role="img" aria-label="Workforce diversity donut chart">
            <g transform="translate(26,19)">
              <circle r="12" fill="none" stroke="#1d63b8" stroke-width="5"/>
              <circle r="12" fill="none" stroke="#5fa0de" stroke-width="5" stroke-dasharray="30.2 75.4" stroke-dashoffset="0" transform="rotate(-90)"/>
              <circle r="12" fill="none" stroke="#9cc6ee" stroke-width="5" stroke-dasharray="6 75.4" stroke-dashoffset="-18" transform="rotate(-90)"/>
            </g>
            <text x="0" y="20" font-family="Carlito,sans-serif" font-size="2.6">White</text>
            <text x="0" y="23" font-family="Carlito,sans-serif" font-size="2.6">60%</text>
            <text x="42" y="6" font-family="Carlito,sans-serif" font-size="2.4">Middle-Eastern 8%</text>
            <text x="42" y="15" font-family="Carlito,sans-serif" font-size="2.4">Hispanic 8%</text>
            <text x="42" y="26" font-family="Carlito,sans-serif" font-size="2.4">Asian 24%</text>
          </svg>
          <div class="stat-title">Age</div>
          <svg width="70" height="22" viewBox="0 0 70 22" role="img" aria-label="Employee age distribution">
            <circle cx="10" cy="8" r="4.5" fill="#2a6fc0"/><text x="10" y="9" font-size="2.4" text-anchor="middle" fill="#fff" font-family="Carlito,sans-serif">32%</text>
            <circle cx="27" cy="8" r="7" fill="#1d4f9a"/><text x="27" y="9" font-size="3" text-anchor="middle" fill="#fff" font-family="Carlito,sans-serif">56%</text>
            <circle cx="44" cy="8" r="3.2" fill="#9cc6ee"/><text x="44" y="9" font-size="2.2" text-anchor="middle" fill="#1d3b6e" font-family="Carlito,sans-serif">12%</text>
            <text x="10" y="20" font-size="2.3" text-anchor="middle" font-family="Carlito,sans-serif">25 – 44</text>
            <text x="27" y="20" font-size="2.3" text-anchor="middle" font-family="Carlito,sans-serif">45 – 64</text>
            <text x="44" y="20" font-size="2.3" text-anchor="middle" font-family="Carlito,sans-serif">65+</text>
          </svg>
        </div>
        <div>
          <div class="stat-title">Gender</div>
          <div class="gender">
            <div>Female<div class="ring">60%</div></div>
            <div>Male<div class="ring">40%</div></div>
          </div>
          <div class="stat-title" style="margin-top:6px">Executive Officers</div>
          <div class="people" role="img" aria-label="Icons of three executive officers"></div>
          <div class="small-note" style="font-weight:400;margin:1px 0 5px">2 of 3 are women</div>
          <div class="stat-title">Board Composition</div>
          <div class="small-note">50% women (3 directors)<br>One woman from an<br>underrepresented community</div>
        </div>
      </div>
      <p>As a result of our company culture and commitment to attract, motivate, reward, and retain our employees, we believe our workforce is strong and stable. The average tenure of our employees is 10 years or more.</p>
      <p>Annually, we monitor employee satisfaction by requesting all employees to participate in an engagement survey. Our executive team analyzes the results and makes incremental changes based on employee feedback. In 2021, we received 21 completed surveys. Employee satisfaction averages 90%.</p>
      <div class="sec">Anti-Harassment and Non-Discrimination</div>
      <p>Harbor Crest is committed to maintaining a work environment that is free from unlawful discrimination, harassment, and retaliation. In keeping with this commitment, our company does not tolerate unlawful discrimination against, or harassment of, an applicant, employee, client, customer, or vendor based on any protected characteristic. We prohibit retaliation of any kind against an individual who complains of suspected harassment or discrimination, or who otherwise engages in protected activity.</p>
      <p>In accordance with state law, all employees are required to complete anti-harassment and anti-abusive conduct training courses on a bi-annual basis.</p>
    </div>
    <div class="foot-rule"></div><div class="page-no">Page | 2</div>
    <div class="foot-brand"><div class="dot"></div><span>HCP</span></div>
  </section>

  <section class="page" style="left:531px;top:600px">
    <div class="brand-corner"><div class="sq"></div><span>HCP</span></div><div class="head-rule"></div>
    <div class="content">
      <div class="sec" style="margin-top:1px">Anti-Corruption</div>
      <p>Harbor Crest expects our employees and persons with whom we do business, including lessees, borrowers, and financing sources, to act ethically and with integrity. We do not tolerate corruption in any form. We will not engage in any form of corrupt practices including, without limitation, extortion, fraud, impersonation, false declarations, bribery, money laundering, supporting or involvement with terrorist or organized crime organizations or activities. Our personnel will not offer, solicit or accept bribes or kickbacks involving any government official or third party with the intention of obtaining or retaining a business advantage. We do not permit improper or excessive payments in dealing with the government or private sector. Our employees are expected to observe all government rules, regulations and restrictions on gifts and entertainment.</p>
      <div class="sec">Compensation and Benefits</div>
      <p>Harbor Crest recognizes the importance of committing to ensuring a living wage for all employees by complying with the national wage regulations, such as the minimum wage and overtime payments. We compensate employees at competitive rates, in all cases at or above applicable minimum wage levels including overtime for eligible employees.</p>
      <p>We believe the employee health care and other benefits we offer meet or exceed market standards. For qualified employees, we offer a 401(k) retirement plan with an employer contribution matching program and an opportunity to earn discretionary bonuses, restricted stock awards and performance-based unit awards. We offer flexible working locations for certain job functions.</p>
      <p>We are committed to the health, safety, and wellness of our employees. We pay 100% of the health care premiums for employees and all eligible dependents. The benefits we offer include medical, dental, and vision coverage, paid time off, paid holidays, bereavement leave, and employer-funded life and disability insurance. We also offer an employee assistance program to support our employees' mental health and well-being.</p>
      <div class="sec">Diversity, Equity &amp; Inclusion</div>
      <p>As an equal opportunity employer, Harbor Crest values the diversity of the unique individuals who comprise our team from workforce level to senior level and extending to our Board of Directors. We do not discriminate based on an individual's race, gender, age, color, religion, national origin, mental or physical disability, sexual orientation, ancestry, genetic information, military or veteran status, creed, pregnancy, marital status, citizenship, gender identity, gender expression or any other status protected by applicable law. This statement extends to specifically respect and protect minority groups and women's rights under the internationally endorsed UN Guiding Principles on Business and Human Rights.</p>
    </div>
    <div class="foot-rule"></div><div class="page-no">Page | 3</div>
    <div class="foot-brand"><div class="dot"></div><span>HCP</span></div>
  </section>

  <section class="page" style="left:744px;top:600px">
    <div class="brand-corner"><div class="sq"></div><span>HCP</span></div><div class="head-rule"></div>
    <div class="content">
      <p>Our company will provide reasonable accommodations for qualified individuals with disabilities and medical conditions. Employment decisions at our company are based on merit, qualifications, and abilities.</p>
      <div class="sec">Employee Safety and Health</div>
      <p>Employee safety and health is an important element of our working environment, and we are dedicated to creating and maintaining a safe and healthy working environment.</p>
      <p>We discourage employees from lifting heavy objects and we encourage good nutrition by providing healthy snacks for employees. We also make adjustable stand-up desks available and encourage their use by employees. Smoking is prohibited in our offices. Hand sanitizer stations are located throughout the office.</p>
      <p>A safe and healthy environment includes access to clean sanitary facilities and drinking water as a fundamental human right. Our corporate headquarters provides employees with tri-temp purified water from reverse osmosis water systems plumbed into the wall, eliminating the need for plastic or glass refill bottles.</p>
      <p>Over the past 30 years, Harbor Crest has incurred one incidence of workman's compensation settlement for an injury, and zero occupational diseases or workplace-related fatalities.</p>
      <div class="sec">Freedom of Association</div>
      <p>We recognize and do not interfere with our employees' right to self-organization, to form, join, or assist labor organizations, to bargain collectively through representatives of their own choosing, and to engage in other concerted activities for the purpose of collective bargaining or other mutual aid or protection.</p>
      <div class="sec">Philanthropic Support</div>
      <p>Harbor Crest supports charitable initiatives ultimately benefitting our operating partners, their residents and employees, and the seniors housing and care industry. This support includes industry associations on various levels and customer employee assistance funds.</p>
      <p>Many employees support our local community through voluntary contributions to annual company-wide holiday season philanthropies. We sponsor and organize a team to participate in a local memory walk.</p>
      <div class="sec">Political Contributions</div>
      <p>Our Code of Business Conduct and Ethics prohibits contributions of company assets to any political candidate, political action committees, political party, or ballot measure without the permission of our Chief Executive Officer or Board of Directors.</p>
    </div>
    <div class="foot-rule"></div><div class="page-no">Page | 4</div>
    <div class="foot-brand"><div class="dot"></div><span>HCP</span></div>
  </section>

  <section class="page" style="left:957px;top:600px">
    <div class="brand-corner"><div class="sq"></div><span>HCP</span></div><div class="head-rule"></div>
    <div class="content">
      <div class="sec" style="margin-top:3px">Stakeholder Consultation and Engagement</div>
      <p>Harbor Crest distributes a proxy statement and holds an annual meeting to provide stockholders the opportunity to engage with the company. Other stakeholders may contact us online at <span class="link">www.harborcrest.example/contact</span>.</p>
      <div class="sec">Training and Education</div>
      <p>Harbor Crest invests in employee development and training by providing access to in-class and online learning and by promoting participation in professional seminars and continuing education. We encourage attendance at industry conferences where employees can choose from various presentations, seminars, and workshops. We reimburse employees who attend these industry conferences.</p>
      <p>For employees with at least one year of service, we grant up to three days leave to take professional licensing examinations. We pay for the annual renewal fee for registration for a professional license. We encourage membership in professional societies.</p>
      <div class="sec">Complaints</div>
      <p>Harbor Crest has implemented a whistleblower hotline and dedicated email address to enable all interested parties, including employees, to submit confidential complaints, concerns, unethical business practices, violations or suspected violations for all matters pertaining to accounting, internal control, or auditing. Our company will not tolerate retaliation for whistleblower reports made in good faith.</p>
      <p>Please direct questions and input about this policy to Jordan Reyes <span class="link">jordan.reyes@harborcrest.example</span>.</p>
      <p class="adopted">Adopted &nbsp;&nbsp;&nbsp;&nbsp;&nbsp;&nbsp;&nbsp;&nbsp;&nbsp;&nbsp;&nbsp;&nbsp;, 2022</p>
    </div>
    <div class="foot-rule"></div><div class="page-no">Page | 5</div>
    <div class="foot-brand"><div class="dot"></div><span>HCP</span></div>
  </section>

  <!-- FILE 4 · Vendor Code of Conduct -->
  <section class="page" style="left:105px;top:893px">
    <div class="brand-corner"><div class="sq"></div><span>HCP</span></div><div class="head-rule"></div>
    <div class="content">
      <div class="doc-title" style="margin-top:2px;font-size:5.4px">HARBOR CREST PROPERTIES, INC.</div>
      <div class="doc-sub blue">Vendor Code of Conduct</div>
      <p>At Harbor Crest Properties, Inc. ("HCP"), we are committed to operating our business in an ethical manner and with a strong sense of integrity consistent with our Code of Business Conduct and Ethics and other company policies and guidelines. We expect our partners, suppliers, and vendors (each, a "Vendor") to demonstrate a similar commitment by adhering to this Vendor Code of Conduct.</p>
      <p>The development and maintenance of this Vendor Code of Conduct is a company-wide effort overseen by the Board of Directors through its Environmental, Social and Governance Committee. The standards reflected in this Vendor Code of Conduct are consistent with the standards we follow in our Human and Labor Rights Policy.</p>
      <p>This Code has been developed by reference to the United Nations Sustainable Development Goals, the International Labour Organization's eight fundamental conventions, and other established frameworks. We encourage Vendors to utilize these and other recognized sources to engage in ethical business practices.</p>
      <div class="sec" style="font-size:3.3px">Treatment of Employees</div>
      <div class="sub-sec">Anti-Harassment and Non-Discrimination</div>
      <p class="indent">Vendors must maintain a work environment that is free from unlawful discrimination, harassment, and retaliation. In keeping with this commitment, we do not tolerate unlawful discrimination against, or harassment of, an applicant, employee, client, customer, or Vendor based on any protected characteristic. Vendors should provide an environment that allows employees to ask questions or raise concerns without fear of retaliation, and should prohibit retaliation of any kind against any individual who complains of suspected harassment or discrimination.</p>
      <div class="sub-sec">Child Labor</div>
      <p class="indent">In accordance with International Labour Organization Convention No. 138, Vendors shall not employ child labor and should take the necessary preventive measures to ensure that they do not employ anyone under the applicable legal minimum age of employment.</p>
      <div class="sub-sec">Compensation and Working Hours</div>
      <p class="indent">Vendors must comply with applicable wage and benefits laws and regulations governing work hours and overtime. We believe Vendors should offer a fair living wage to all employees and encourage Vendors to abide by international standards on working hours that permit adequate time for rest and leisure.</p>
    </div>
    <div class="foot-rule"></div><div class="page-no">Page | 1</div>
    <div class="foot-brand"><div class="dot"></div><span>HCP</span></div>
  </section>

  <section class="page" style="left:318px;top:893px">
    <div class="brand-corner"><div class="sq"></div><span>HCP</span></div><div class="head-rule"></div>
    <div class="content">
      <div class="sub-sec" style="margin-top:1px">Diversity, Equal Opportunity and Gender Equality</div>
      <p class="indent">Vendors must not discriminate based on an individual's race, gender, age, color, religion, national origin, mental or physical disability, sexual orientation, ancestry, genetic information, military or veteran status, creed, pregnancy, marital status, citizenship, gender identity, gender expression, or any other status protected by applicable law.</p>
      <div class="sub-sec">Forced Labor</div>
      <p class="indent">We do not tolerate the use of slavery and other forms of forced or coerced labor or servitude, including prison and human trafficking. We will not knowingly work with a Vendor who engages in these practices. All work must be performed under and in accordance with contracts and arrangements that have been entered into voluntarily.</p>
      <div class="sub-sec">Freedom of Association</div>
      <p class="indent">We expect Vendors to recognize, and not interfere with, their employees' right to self-organization, to form, join, or assist labor organizations, to bargain collectively through representatives of their own choosing, and to engage in other concerted activities for the purpose of collective bargaining or other mutual aid or protection.</p>
      <div class="sub-sec">Safety and Health</div>
      <p class="indent">Employee safety and health is an important element of our working environment. We expect Vendors to provide a safe and healthy working environment that includes access to clean sanitary facilities and drinking water as a fundamental human right.</p>
      <div class="sec" style="font-size:3.3px">Ethics and Business Practices</div>
      <div class="sub-sec">Anti-Corruption and Anti-Bribery</div>
      <p class="indent">We do not tolerate corruption or bribery in any form, and we expect Vendors to comply with requirements of all applicable anti-corruption laws, including but not limited to national foreign corrupt practices laws. Vendors must not pay or offer bribes or kickbacks to any company representative, government official or third party with the intention of obtaining or retaining an unfair business advantage.</p>
      <div class="sub-sec">Confidentiality and Data Protection</div>
      <p class="indent">Vendors are entrusted with proprietary and personal information and should uphold all legal obligations and otherwise ensure protection of all sensitive information, including confidential, proprietary, and personal information. Information should not be used for any purpose beyond the scope of the business arrangement without prior authorization.</p>
    </div>
    <div class="foot-rule"></div><div class="page-no">Page | 2</div>
    <div class="foot-brand"><div class="dot"></div><span>HCP</span></div>
  </section>

  <section class="page" style="left:531px;top:893px">
    <div class="brand-corner"><div class="sq"></div><span>HCP</span></div><div class="head-rule"></div>
    <div class="content">
      <p class="indent">Vendors should also ensure that information remains private by implementing and maintaining adequate cybersecurity measures and complying with all applicable laws and regulations to mitigate risk of data breach.</p>
      <div class="sub-sec">Environmental Stewardship</div>
      <p class="indent">Harbor Crest recognizes the importance of corporate environmental stewardship and believes Vendors should strive to be environmentally conscious and conduct operations to minimize the impact on water, energy, and other natural resources. We encourage Vendors to adhere to best practices to protect and improve our shared environment.</p>
      <div class="sub-sec">Legal and Regulatory Practices</div>
      <p class="indent">We expect Vendors to conduct their business in full compliance with laws and regulations applicable to their business. Vendors should be cooperative with the regulators and strive to implement best practices to avoid violations of law.</p>
      <div class="sec" style="font-size:3.3px">Compliance</div>
      <p>Vendors are expected to self-monitor and may be requested to demonstrate compliance by Harbor Crest. If a Vendor has questions or concerns about this Vendor Code of Conduct, the Vendor should seek guidance from their company relationship contact. We also have implemented a whistleblower hotline and dedicated email address to enable all interested parties to submit confidential complaints, concerns, unethical business practices, violations or suspected violations for all matters pertaining to our Code of Business Conduct and Ethics and this Vendor Code of Conduct. We will not tolerate retaliation for whistleblower reports made in good faith.</p>
      <p>Harbor Crest is committed to continuously reviewing and updating this Vendor Code of Conduct, and it is subject to modification from time to time.</p>
      <p>The contents of this Vendor Code of Conduct are additional to and do not in any way affect or prejudice any of our rights and remedies under a relevant contract, if any, with a Vendor.</p>
      <p class="adopted">Adopted &nbsp;&nbsp;&nbsp;&nbsp;&nbsp;&nbsp;&nbsp;&nbsp;&nbsp;&nbsp;&nbsp;&nbsp;, 2022</p>
    </div>
    <div class="foot-rule"></div><div class="page-no">Page | 3</div>
    <div class="foot-brand"><div class="dot"></div><span>HCP</span></div>
  </section>

</div>
</body>
</html>
```